Premium Food Label Design – High-End Boutique Jar Labels (3 Sizes)

I require a complete jar label redesign across three sizes:
75mm x 130mm (Large & Medium)
55mm x 120mm (Small)
45mm x 120mm (XS)

The design must feel professional, modern, elegant, and high-end boutique.
Primary aesthetic: white, minimal, refined, with accents in soft brown and gold/bronze. (see prefer colours of logo in OLD LABEL PDF)
Transparent background required.

I have attached my current label for wording reference only — I want to move away from the kraft look entirely.
The label must include all existing details, plus a dedicated space to manually add batch number and date.

IMPORTANT: Final files must be supplied as editable Adobe Illustrator (.AI) files with live text layers (not outlined) so I can update them as needed.
Logo is attached. I’m open to a fresh, elevated design direction aligned with a premium brand feel.

Target Market(s)

People who appreciate high-end, thoughtfully crafted food and are willing to pay for quality

Industry/Entity Type

Gourmet Food / Artisan Food Packaging

Requirements
Must have
• Premium, minimal aesthetic, Strong typography hierarchy, White background, Consistency across 3 sizes
Nice to have
• Elevated “Tide Lantern” styling
Should not have
• No bright or bold colours, No clutter or overcrowding, No heavy borders or thick frames,No “homemade/craft” fonts

```html
<!DOCTYPE html>
<html lang="en">
<head>
<meta charset="utf-8">
<title>Ember Pantry – Tomato Relish Labels</title>
<link rel="stylesheet" href="https://fonts.googleapis.com/css2?family=Josefin+Sans:wght@300;400;600&family=EB+Garamond:ital@1&display=swap">
<style>
  :root {
    --page: #ffffff;
    --cream: #f4f2e3;
    --cream-deep: #e9e7cf;
    --cocoa: #42241a;
    --copper-dark: #7a3a1c;
    --copper: #a9572d;
    --copper-light: #c87a4b;
    --ink: #3a2a22;
    --tan: #a88a6a;
    --white: #ffffff;
  }
  * { box-sizing: border-box; margin: 0; padding: 0; }
  html, body { width: 1200px; height: 1200px; overflow: hidden; background: var(--page); }
  body {
    font-family: "Josefin Sans", sans-serif;
    color: var(--ink);
    display: flex;
    align-items: center;
    justify-content: center;
    gap: 22px;
  }
  .label {
    position: relative;
    background: linear-gradient(135deg, var(--cream) 0%, var(--cream-deep) 50%, var(--cream) 100%);
    border-radius: 6px;
    overflow: hidden;
  }
  .label--large  { width: 360px; height: 208px; font-size: 10px; }
  .label--medium { width: 380px; height: 172px; font-size: 9.6px; }
  .label--small  { width: 380px; height: 142px; font-size: 8.2px; }

  .brand-tag {
    position: absolute;
    left: 17%;
    top: 0;
    width: 27%;
    height: 52%;
    background: var(--cocoa);
    clip-path: polygon(0 0, 100% 0, 100% 100%, 50% 90%, 0 100%);
    display: flex;
    align-items: center;
    justify-content: center;
    gap: 0.4em;
  }
  .brand-tag__dot { width: 0.6em; height: 0.6em; border-radius: 50%; background: var(--copper-light); }
  .brand-tag__name {
    color: var(--copper-light);
    font-weight: 400;
    font-size: 1.15em;
    letter-spacing: 0.12em;
    text-align: center;
    line-height: 1.2;
  }

  .intention {
    position: absolute;
    left: 52%;
    right: 3%;
    top: 0;
    height: 52%;
    display: flex;
    flex-direction: column;
    justify-content: center;
    text-align: center;
    font-weight: 300;
    font-size: 0.78em;
    line-height: 1.65;
  }
  .intention__title { font-weight: 400; font-size: 1.05em; }

  .band {
    position: absolute;
    left: 0; right: 0;
    top: 52%;
    height: 17%;
    background: linear-gradient(90deg, var(--copper-dark), var(--copper) 30%, var(--copper-light) 55%, var(--copper) 80%, var(--copper-dark));
    display: flex;
    align-items: center;
    color: var(--white);
  }
  .band__title {
    width: 50%;
    text-align: center;
    font-size: 1.7em;
    font-weight: 400;
    letter-spacing: 0.05em;
    color: var(--cocoa);
  }
  .band__ingredients {
    width: 50%;
    text-align: center;
    font-size: 0.78em;
    font-weight: 300;
    line-height: 1.3;
  }
  .band__ingredients strong { font-weight: 400; display: block; }

  .details {
    position: absolute;
    left: 0; right: 0;
    top: 69%;
    bottom: 0;
    display: flex;
  }
  .details__left {
    width: 31%;
    margin-left: 3%;
    display: flex;
    flex-direction: column;
    align-items: center;
    justify-content: center;
    gap: 0.35em;
  }
  .choice {
    font-size: 1.05em;
    letter-spacing: 0.04em;
    padding-bottom: 0.2em;
    border-bottom: 1px solid var(--ink);
  }
  .made-with-love { font-family: "EB Garamond", serif; font-style: italic; color: var(--tan); font-size: 0.95em; }
  .weight { font-size: 0.95em; margin-top: 0.5em; }

  .details__right {
    flex: 1;
    padding: 0.9em 4% 0.6em 6%;
    display: flex;
    flex-direction: column;
    justify-content: space-between;
    font-size: 0.62em;
    text-align: center;
  }
  .storage { font-weight: 400; letter-spacing: 0.02em; }
  .fill-in { display: flex; gap: 1.2em; justify-content: flex-start; padding-left: 0.5em; }
  .fill-in__line { display: inline-block; width: 7em; border-bottom: 1px solid var(--tan); }
  .maker { line-height: 1.6; }
</style>
</head>
<body>

  <article class="label label--large">
    <div class="brand-tag"><span class="brand-tag__dot"></span><span class="brand-tag__name">EMBER<br>PANTRY</span></div>
    <div class="intention">
      <p class="intention__title">Tide Lantern</p>
      <p>What is made with love is felt in return.<br>May this Relish nourish more than the meal -<br>bringing comfort, connection and joy to every<br>moment shared.</p>
    </div>
    <div class="band">
      <h1 class="band__title">TOMATO RELISH</h1>
      <p class="band__ingredients"><strong>Ingredients:</strong>Tomatoes, Onion, Sugar, Vinegar, Salt, Spices,<br>&amp; Thickener (Cornflour)</p>
    </div>
    <div class="details">
      <div class="details__left">
        <p class="choice">POPULAR CHOICE</p>
        <p class="made-with-love">Made with Love</p>
        <p class="weight">375g</p>
      </div>
      <div class="details__right">
        <p class="storage">STORAGE: KEEP REFRIGERATED ONCE OPENED!</p>
        <p class="fill-in"><span>Batch: # <span class="fill-in__line"></span></span><span>Date: # <span class="fill-in__line"></span></span></p>
        <p class="maker">Made by: Ember Pantry, QLD, Australia<br>www.emberpantry.com | info@emberpantry.com</p>
      </div>
    </div>
  </article>

  <article class="label label--medium">
    <div class="brand-tag"><span class="brand-tag__dot"></span><span class="brand-tag__name">EMBER<br>PANTRY</span></div>
    <div class="intention">
      <p class="intention__title">Tide Lantern</p>
      <p>What is made with love is felt in return.<br>May this Relish nourish more than the meal -<br>bringing comfort, connection and joy to every<br>moment shared.</p>
    </div>
    <div class="band">
      <h1 class="band__title">TOMATO RELISH</h1>
      <p class="band__ingredients"><strong>Ingredients:</strong>Tomatoes, Onion, Sugar, Vinegar, Salt, Spices,<br>&amp; Thickener (Cornflour)</p>
    </div>
    <div class="details">
      <div class="details__left">
        <p class="choice">POPULAR CHOICE</p>
        <p class="made-with-love">Made with Love</p>
        <p class="weight">375g</p>
      </div>
      <div class="details__right">
        <p class="storage">STORAGE: KEEP REFRIGERATED ONCE OPENED!</p>
        <p class="fill-in"><span>Batch: # <span class="fill-in__line"></span></span><span>Date: # <span class="fill-in__line"></span></span></p>
        <p class="maker">Made by: Ember Pantry, QLD, Australia<br>www.emberpantry.com | info@emberpantry.com</p>
      </div>
    </div>
  </article>

  <article class="label label--small">
    <div class="brand-tag"><span class="brand-tag__dot"></span><span class="brand-tag__name">EMBER<br>PANTRY</span></div>
    <div class="intention">
      <p class="intention__title">Tide Lantern</p>
      <p>What is made with love is felt in return.<br>May this Relish nourish more than the meal - bringing<br>comfort, connection and joy to every moment shared.</p>
    </div>
    <div class="band">
      <h1 class="band__title">TOMATO RELISH</h1>
      <p class="band__ingredients"><strong>Ingredients:</strong>Tomatoes, Onion, Sugar, Vinegar, Salt, Spices,<br>&amp; Thickener (Cornflour)</p>
    </div>
    <div class="details">
      <div class="details__left">
        <p class="choice">POPULAR CHOICE</p>
        <p class="made-with-love">Made with Love</p>
        <p class="weight">375g</p>
      </div>
      <div class="details__right">
        <p class="storage">STORAGE: KEEP REFRIGERATED ONCE OPENED!</p>
        <p class="fill-in"><span>Batch: # <span class="fill-in__line"></span></span><span>Date: # <span class="fill-in__line"></span></span></p>
        <p class="maker">Made by: Ember Pantry, QLD, Australia<br>www.emberpantry.com | info@emberpantry.com</p>
      </div>
    </div>
  </article>

</body>
</html>
```